Custom Cabinet Shop Needs a website design

Hi,
We need a website for a Custom Cabinet Shop and Cabinet parts manufacturing business.
The business has two sides to it. One side provides custom Kitchens, vanities, entertainment units, offices and what not to homeowners and contractors.
The 2nd side of the business provides built to order cabinet boxes and other parts required to put together a project to other cabinet shops, small contractors looking to install there own cabinets.
Website will need a Gallery to display work.
Color scheme to go well with logo.
current website is www.brambleoakcustomcabinets.com
being changed to www.brambleoak.ca
Logo Included in attached files.
Tagline "Joinery with Spirit"
Mission Statement "Our passion is to deliver inspired cabinetry solutions to suit all your needs, supported by our phenomenal star class customer service"
The website should convey quality and professionalism.
Thank you.
Homeowners/ Contractors
Entertainment

```html
<!DOCTYPE html>
<html lang="en">
<head>
<meta charset="utf-8">
<title>Brambleoak Custom Cabinets</title>
<link href="https://fonts.googleapis.com/css2?family=Encode+Sans+Condensed:wght@300;400;600;700&family=Open+Sans:wght@400;600&display=swap" rel="stylesheet">
<style>
:root{
  --wood:#3a2a20;
  --orange:#ee5a24;
  --ink:#2b2b2b;
  --text:#5a5a5a;
  --muted:#8c8c8c;
  --light:#f7f7f7;
  --footer:#151515;
  --rule:#c9c9c9;
}
*{margin:0;padding:0;box-sizing:border-box}
html,body{width:1003px;height:1200px;overflow:hidden}
body{background:linear-gradient(90deg,#2e211a,#45332a 30%,#3a2a20 60%,#4a372b);font-family:"Encode Sans Condensed",sans-serif;color:var(--text);position:relative}
.page{position:absolute;left:75px;top:0;width:853px;height:1200px;background:#fff}
.abs{position:absolute}
.header{left:0;top:0;width:853px;height:120px;background:#fafafa}
.logo{left:18px;top:40px;display:flex;align-items:center;gap:8px}
.logo .mark{width:22px;height:22px;border-radius:50%;background:var(--orange)}
.logo .name{font-weight:700;font-size:27px;color:var(--ink);letter-spacing:.5px}
.util{right:18px;top:16px;display:flex;gap:20px;font-family:"Open Sans",sans-serif;font-size:9px;color:#555}
.util span{display:flex;align-items:center;gap:5px}
.util i{width:9px;height:9px;background:#555;border-radius:2px;display:inline-block}
.phone{right:18px;top:44px;font-size:24px;color:var(--ink);font-weight:400}
.phone b{color:var(--orange);font-weight:400}
.nav{right:18px;top:82px;display:flex;gap:40px;font-size:15.5px;color:#444;align-items:center}
.nav .active{background:var(--orange);color:#fff;padding:3px 14px;border-radius:2px}
.hero{left:0;top:120px;width:853px;height:361px;background:linear-gradient(135deg,#1f2a38 0%,#5a4530 45%,#8a6a48 65%,#b69a7a 100%)}
.caption{left:0;top:435px;width:853px;height:46px;background:rgba(0,0,0,.8)}
.caption h1{position:absolute;left:16px;top:4px;font-size:35px;font-weight:300;color:#fff;text-transform:uppercase;letter-spacing:-.5px}
.caption h1 strong{font-weight:700}
.dots{position:absolute;right:18px;top:19px;display:flex;gap:4px}
.dots i{width:7px;height:7px;border-radius:50%;background:#fff}
.dots i.on{background:var(--orange)}
.col h2{font-size:17px;font-weight:600;color:var(--orange);border-left:6px solid var(--orange);padding-left:10px;line-height:16px}
.col .body{position:absolute;top:29px;left:0;width:240px;height:126px;border-left:3px dotted #ddd;padding-left:14px;padding-top:12px;font-size:11px;line-height:18.4px;color:var(--text)}
.btn{position:absolute;background:var(--orange);color:#fff;font-size:12px;font-weight:600;padding:5px 10px;border-radius:2px}
.gallery{left:0;top:726px;width:853px;height:305px;background:var(--light)}
.gallery h2{position:absolute;left:17px;top:33px;font-size:17px;font-weight:400;color:var(--orange)}
.gallery .line{position:absolute;left:117px;top:43px;width:681px;border-top:3px dotted #ddd}
.arrows{position:absolute;right:17px;top:38px;display:flex;gap:2px}
.arrows span{width:14px;height:14px;background:#777;color:#fff;font-size:10px;text-align:center;line-height:14px}
.arrows span+span{background:#222}
.card{position:absolute;top:76px;width:192px;text-align:center}
.card .ph{height:143px}
.card h3{font-size:13.5px;font-weight:400;color:var(--ink);margin-top:5px}
.card p{font-size:9px;color:var(--muted);font-family:"Open Sans",sans-serif}
.card .bar{height:2px;background:var(--rule);margin:4px 2px 0}
.card.sel h3{color:var(--orange)}
.card.sel .bar{background:var(--orange)}
.footer{left:0;top:1031px;width:853px;height:169px;background:var(--footer);color:#fff;text-align:center}
.fnav{position:absolute;top:35px;left:0;width:100%;display:flex;justify-content:center;gap:33px;font-size:13px}
.fnav b{font-weight:700}
.social{position:absolute;top:74px;left:0;width:100%;display:flex;justify-content:center;gap:5px}
.social i{width:25px;height:25px;border-radius:50%;background:#fff}
.copy{position:absolute;top:122px;width:100%;font-size:10.5px}
</style>
</head>
<body>
<div class="page">
  <header class="abs header">
    <div class="abs logo"><span class="mark"></span><span class="name">BRAMBLEOAK</span></div>
    <div class="abs util"><span><i></i>My Favorites</span><span><i></i>Brambleoak.ca</span><span><i></i>For Dealers</span></div>
    <div class="abs phone"><b>Call Us</b> : 403-555-0148</div>
    <nav class="abs nav"><span class="active">Home</span><span>Our Gallery</span><span>Our Services</span><span>Warranty</span><span>Contact Us</span></nav>
  </header>

  <div class="abs hero" role="img" aria-label="Photo of a basement bar with live-edge wood counter, stools, pendant lights and wine rack"></div>
  <div class="abs caption">
    <h1>Joinery with <strong>Spirit</strong></h1>
    <div class="dots"><i></i><i class="on"></i><i></i><i></i></div>
  </div>

  <section class="abs col" style="left:17px;top:521px">
    <h2>ABOUT US</h2>
    <div class="body">Lorem ipsum dolor sit amet, consectetur adipiscing elit, sed do eiusmod tempor incididunt ut labore et dolore magna aliqua. Ut enim ad minim veniam, quis nostrud exercitation ullamco laboris nisi ut aliquip ex ea commodo consequat. Duis aute irure dolor in reprehenderit in voluptate velit esse</div>
  </section>
  <section class="abs col" style="left:289px;top:521px">
    <h2>FINEST QUALITY MATERIALS</h2>
    <div class="body">Lorem ipsum dolor sit amet, consectetur adipiscing elit, sed do eiusmod tempor incididunt ut labore et dolore magna aliqua enim ad minim veniam is quis exercitation ullamco.</div>
    <span class="btn" style="left:172px;top:130px">Read More</span>
  </section>
  <section class="abs col" style="left:558px;top:521px">
    <h2>RESIDENTIAL</h2>
    <div class="body">Here at Brambleoak Custom Cabinets we are proud to be involved in the custom cabinet market. By employing and partnering up with local artisans we are able to deliver a product.</div>
    <span class="btn" style="left:177px;top:130px">Read More</span>
  </section>

  <section class="abs gallery">
    <h2>OUR GALLERY</h2>
    <div class="line"></div>
    <div class="arrows"><span>‹</span><span>›</span></div>
    <div class="card" style="left:18px"><div class="ph" role="img" aria-label="Photo of a dark cherry kitchen with island" style="background:linear-gradient(160deg,#c9c3bb,#5a2a1c 55%,#7a3a22)"></div><h3>Lorem Ipsum Dolor</h3><p>Lorem ipsum</p><div class="bar"></div></div>
    <div class="card sel" style="left:227px"><div class="ph" role="img" aria-label="Photo of a maple kitchen with dark island and pendants" style="background:linear-gradient(160deg,#ddd6cc,#8a5a34 55%,#3a2a22)"></div><h3>Sit Amet Consectetur</h3><p>Lorem Ipsum</p><div class="bar"></div></div>
    <div class="card" style="left:436px"><div class="ph" role="img" aria-label="Photo of a red wood kitchen with ornate island" style="background:linear-gradient(170deg,#efe6da,#8a2a14 50%,#c9b49a)"></div><h3>Adipisicing Elit</h3><p>Lorem Ipsum</p><div class="bar"></div></div>
    <div class="card" style="left:643px"><div class="ph" role="img" aria-label="Photo of an open kitchen with wood cabinets and island" style="background:linear-gradient(160deg,#e6e2dc,#9a6a44 50%,#6a4a30)"></div><h3>Labore Et Dolore</h3><p>Lorem Ipsum</p><div class="bar"></div></div>
  </section>

  <footer class="abs footer">
    <nav class="fnav"><b>Home</b><span>Our Gallery</span><span>Our Services</span><span>Warranty</span><span>Contact Us</span></nav>
    <div class="social"><i></i><i></i><i></i><i></i><i></i><i></i></div>
    <p class="copy">Copyrights © 2015. Brambleoak Custom Cabinets . All Rights Reserved</p>
  </footer>
</div>
</body>
</html>
```